Business Cards - Brightpath Horizon

need to design unique business card for my mortgage business. I need to design credit card style business card for my business or any unique idea that you might have

Target Market(s)

Home Loan customers

Industry/Entity Type

Mortgage Brokerage

Contact Information for Business Card

please design credit card style or very unique style business card

Colors

Designer to choose colors to be used in the design.

Requirements
Must have
• Name
• position
• Phone number
• fax number
• email address
• website address
• social media address
• All above fields will be provided once design in finalised

```html
<!DOCTYPE html>
<html lang="en">
<head>
<meta charset="utf-8">
<title>Brightpath Horizon – Business Card</title>
<link rel="stylesheet" href="https://fonts.googleapis.com/css2?family=Roboto:wght@400;500;700&family=Share+Tech+Mono&display=swap">
<style>
  :root {
    --stage: #2a2a2a;
    --card-front: #f4f4f4;
    --brand-blue: #1f3fc6;
    --web-grey: #5a5a5a;
    --card-deep: #020c2a;
    --card-mid: #0c3f6e;
    --card-glow: #1a6b9b;
    --ink-light: #ffffff;
  }
  * { margin: 0; padding: 0; box-sizing: border-box; }
  html, body { width: 1200px; height: 960px; overflow: hidden; }
  body {
    background: var(--stage);
    font-family: "Roboto", Arial, sans-serif;
    position: relative;
  }
  .card {
    position: absolute;
    left: 320px;
    width: 600px;
    border-radius: 18px;
  }
  .card-front {
    top: 100px;
    height: 350px;
    background: var(--card-front);
  }
  .front-brand {
    position: absolute;
    left: 0; right: 0; top: 154px;
    display: flex; align-items: center; justify-content: center; gap: 14px;
  }
  .front-brand .mark {
    width: 32px; height: 32px; border-radius: 50%;
    background: var(--brand-blue);
  }
  .front-brand .brand-name {
    font-size: 38px; font-weight: 500; color: var(--brand-blue);
  }
  .front-web {
    position: absolute; left: 0; right: 0; top: 308px;
    text-align: center;
    font-size: 15px; letter-spacing: 7px; color: var(--web-grey);
  }
  .card-back {
    top: 494px;
    height: 342px;
    background:
      radial-gradient(ellipse 55% 90% at 52% 50%, var(--card-glow) 0%, var(--card-mid) 45%, var(--card-deep) 100%);
    color: var(--ink-light);
  }
  .back-brand {
    position: absolute; left: 28px; top: 40px;
    display: flex; align-items: center; gap: 8px;
  }
  .back-brand .mark {
    width: 16px; height: 16px; border-radius: 50%; background: var(--ink-light);
  }
  .back-brand .brand-name { font-size: 20px; font-weight: 500; }
  .address {
    position: absolute; right: 34px; top: 35px;
    font-size: 15px;
  }
  .social {
    position: absolute; right: 34px; top: 66px;
    display: flex; gap: 3px;
  }
  .social span {
    width: 20px; height: 20px; border-radius: 50%; background: var(--ink-light);
  }
  .card-number {
    position: absolute; left: 0; right: 0; top: 145px;
    text-align: center;
    font-family: "Share Tech Mono", "Courier New", monospace;
    font-size: 46px; letter-spacing: 2px; word-spacing: 4px;
  }
  .person { position: absolute; left: 28px; top: 268px; }
  .person .name { font-size: 21px; font-weight: 500; }
  .person .role { font-size: 16px; margin-top: 3px; }
  .contact {
    position: absolute; right: 34px; top: 258px;
    text-align: right; font-size: 15px; line-height: 19px;
  }
</style>
</head>
<body>
  <section class="card card-front">
    <div class="front-brand">
      <span class="mark"></span>
      <span class="brand-name">Brightpath Horizon</span>
    </div>
    <p class="front-web">www.siteaddress.com</p>
  </section>

  <section class="card card-back">
    <div class="back-brand">
      <span class="mark"></span>
      <span class="brand-name">Brightpath Horizon</span>
    </div>
    <p class="address">214 Linden Court, Fairview, Oregon 97024</p>
    <div class="social"><span></span><span></span><span></span><span></span></div>
    <p class="card-number">503 271 9046</p>
    <div class="person">
      <p class="name">DANIEL HART</p>
      <p class="role">CEO/FOUNDER</p>
    </div>
    <div class="contact">
      <p>503 718 2264</p>
      <p>mail@siteaddress.com</p>
      <p>www.siteaddress.com</p>
    </div>
  </section>
</body>
</html>
```